Quintel Packaging Business Card

Project Overview
We are seeking a modern, minimalist business card that effectively represents our company while making a bold and lasting impression. The design should reflect trust, professionalism, and innovation, reinforcing our expertise in custom plastic manufacturing for warehouse and distribution centers.

Provided Assets & Specifications
Logo: We will provide our official logo for integration into the design.
Design Files: Photoshop (PSD) files for our printing specifications will be supplied.

Card Size & Material:
Dimensions: 3.5" x 2"
Material: 1/8" Radius Plastic Business Cards with 1/8" Rounded Corners
Clear plastic background—the design should strategically incorporate transparency.
Orientation: The card should be designed in landscape format for a sleek and professional presentation.

Design Requirements:
Logo Prominence
The logo must be the focal point of the card.
Space should be used effectively to draw attention to the logo while maintaining a minimalist layout.

Clear Plastic Integration
The transparent background should create the illusion of blank space, enhancing the modern and high-quality feel.
Avoid any frosted effects—we do not want white areas to appear semi-transparent.

Minimalist & Impactful
Clean, structured, and easy to read at a glance.
Focus on sharp contrast to ensure legibility and visibility.
The design should instill confidence and reflect our role as a leading plastics manufacturer.

Color Palette & Contrast
Primary Colors: Blue, Black, White, and Grey
Use bold black or blue for text and key elements to ensure they stand out against the clear plastic.
Avoid light, pastel, or neon colors that may fade into the plastic background.
No frosted or semi-transparent white—we do not want a cloudy effect.

Typography & Information Hierarchy
Bold, modern typography—clear, professional, and highly legible.
The business card should highlight:
Company Logo (Primary Focus)
Full Name & Title
Phone Number
Email
Website

Brand Representation
The card should reflect our expertise in manufacturing high-quality custom plastics for large-scale packaging and distribution businesses.
Our clients rely on us to enhance their brand presence through custom plastic solutions, and our business cards should reinforce that sense of precision and trust.

Final Considerations
Utilize the clear plastic effectively to differentiate our brand from standard business cards.
Maintain a sleek, professional aesthetic while ensuring all text and elements remain legible.
The design should align with our industry, conveying reliability and innovation.
We look forward to seeing a design that captures our brand identity, maximizes the clear plastic medium, and makes a strong, professional impact on our clients.

```html
<!DOCTYPE html>
<html lang="en">
<head>
<meta charset="utf-8">
<title>Quintel Packaging Business Card</title>
<link href="https://fonts.googleapis.com/css2?family=Montserrat:wght@400;500;700;800&display=swap" rel="stylesheet">
<style>
  :root {
    --stage: #e6e7e9;
    --card-dark: #333436;
    --card-white: #ffffff;
    --brand-blue: #1b8bc4;
    --ink: #2b2b2b;
    --grey: #a9aaac;
    --edge-blue: #1d8fd0;
  }
  * { box-sizing: border-box; margin: 0; padding: 0; }
  html, body {
    width: 1200px; height: 913px; overflow: hidden;
    background: var(--stage);
    font-family: "Montserrat", Arial, sans-serif;
  }
  .stage { position: relative; width: 1200px; height: 913px; }

  .card {
    position: absolute;
    width: 580px; height: 331px;
    border-radius: 22px;
    overflow: hidden;
    box-shadow: 0 10px 28px rgba(0,0,0,.18);
  }

  /* Front side */
  .card--front {
    left: 60px; top: 60px;
    background: var(--card-dark);
    border-bottom: 5px solid var(--edge-blue);
    display: flex; align-items: center; justify-content: center;
  }
  .front-logo { display: flex; align-items: center; gap: 22px; }
  .front-logo .logo-square {
    width: 70px; height: 70px; background: var(--grey);
  }
  .front-logo .logo-name {
    font-weight: 700; font-size: 46px; line-height: 1.05;
    color: var(--grey); letter-spacing: .5px;
  }

  /* Back side */
  .card--back {
    left: 560px; top: 522px;
    background: var(--card-white);
  }
  .back-logo {
    position: absolute; left: 40px; top: 118px;
    display: flex; align-items: center; gap: 12px;
  }
  .back-logo .logo-square { width: 38px; height: 38px; background: var(--brand-blue); }
  .back-logo .logo-name {
    font-weight: 700; font-size: 23px; line-height: 1.1; color: var(--brand-blue);
  }
  .divider {
    position: absolute; left: 282px; top: 42px;
    width: 2px; height: 170px; background: var(--brand-blue);
  }
  .contact { position: absolute; left: 302px; top: 38px; color: var(--ink); }
  .contact .name {
    font-weight: 800; font-size: 22px; color: var(--brand-blue); letter-spacing: .3px;
  }
  .contact .title { font-size: 13px; margin-bottom: 10px; }
  .contact .address { font-size: 13px; line-height: 1.4; margin-bottom: 8px; }
  .contact ul { list-style: none; font-size: 13px; line-height: 1.5; }
  .contact li { display: flex; align-items: center; gap: 7px; }
  .contact li svg { width: 12px; height: 12px; fill: var(--brand-blue); flex: none; }
  .wave { position: absolute; left: 0; bottom: 0; width: 580px; height: 150px; }
</style>
</head>
<body>
<main class="stage">
  <section class="card card--front" aria-label="Card front">
    <div class="front-logo">
      <span class="logo-square"></span>
      <span class="logo-name">Quintel<br>Packaging</span>
    </div>
  </section>

  <section class="card card--back" aria-label="Card back">
    <div class="back-logo">
      <span class="logo-square"></span>
      <span class="logo-name">Quintel<br>Packaging</span>
    </div>
    <span class="divider"></span>
    <div class="contact">
      <p class="name">MORGAN HALE</p>
      <p class="title">Managing Director</p>
      <p class="address">Your address, City<br>State, Zip 1234</p>
      <ul>
        <li><svg viewBox="0 0 24 24"><path d="M6.6 10.8a15 15 0 0 0 6.6 6.6l2.2-2.2a1 1 0 0 1 1-.25 11.4 11.4 0 0 0 3.6.57 1 1 0 0 1 1 1V20a1 1 0 0 1-1 1A17 17 0 0 1 3 4a1 1 0 0 1 1-1h3.5a1 1 0 0 1 1 1c0 1.25.2 2.45.57 3.57a1 1 0 0 1-.25 1z"/></svg>123 456 789</li>
        <li><svg viewBox="0 0 24 24"><path d="M2 5h20v14H2z M2 5l10 8 10-8" /></svg>info@yourgmail.com</li>
        <li><svg viewBox="0 0 24 24"><circle cx="12" cy="12" r="10"/></svg>www.yourwebsite.com</li>
      </ul>
    </div>
    <svg class="wave" viewBox="0 0 580 150" preserveAspectRatio="none" aria-hidden="true">
      <path d="M0 112 C170 108 330 80 580 12" fill="none" stroke="#2b2b2b" stroke-width="5"/>
      <path d="M0 128 C180 122 360 92 580 22 L580 150 L0 150 Z" fill="#1b8bc4"/>
    </svg>
  </section>
</main>
</body>
</html>
```